Fresh Dwelling Tract Guide needs a new Landing Page

I like to get a landing page or website with 2-3 pages to help target home buyers who are looking to buy homes from builders such as TW Residences, Morvik, P.L. Fennick, etc. The landing page/website to be non-cluttered and be able to explain to home buyers that there are many benefits to include me as their buyer's agent when they buy a brand new home from any builders.
I may want to incorporate a short explanation video (animated) on the landing page and then for the viewer to click on a button that will take them to another page where they can search for new homes from different builders.
Target Market(s)
Home buyers looking to buy brand new home from builders such as TW Residences, Morvik, P.L. Fennick, etc.
Industry/Entity Type
Real Estate
Number of Pages Required
2 page
Font styles to use
Requirements
Must have
- The landing page may have the explanation video at the bottom of the landing page (scrolled down) or there may be a CALL TO ACTION button that takes the viewer to the 2nd page to watch the explanation video. Once they watched the explanation video and are still interested, they can click on another CALL TO ACTION button that will take them to another website that they will be able to search for all the available new homes and register their contact information.
Should not have
- No clutters and no dark colors.

```html
<!DOCTYPE html>
<html lang="en">
<head>
<meta charset="utf-8">
<title>Fresh Dwelling Tract Guide</title>
<link rel="stylesheet" href="https://fonts.googleapis.com/css2?family=Marcellus&family=Jost:wght@400;500&family=Bitter:wght@500&display=swap">
<style>
:root{
  --ink:#3a2a22;
  --text:#222;
  --muted:#555;
  --accent:#e0682b;
  --accent-dark:#c9561c;
  --paper:#ffffff;
  --mist:#f4f5f7;
  --line:#d9d9d9;
  --footer:#333333;
}
*{margin:0;padding:0;box-sizing:border-box}
html,body{width:712px;height:1200px;overflow:hidden;background:var(--paper)}
body{position:relative;font-family:"Jost",sans-serif;color:var(--text)}
.abs{position:absolute}

/* header */
.site-header{left:0;top:0;width:712px;height:66px;background:var(--paper)}
.brand{left:84px;top:16px;display:flex;align-items:center;gap:7px}
.brand-dot{width:14px;height:14px;border-radius:50%;background:var(--accent)}
.brand-name{font-family:"Marcellus",serif;font-size:14px;line-height:15px;color:var(--ink)}
.phone{left:503px;top:25px;display:flex;align-items:center;gap:6px;font-size:11px;color:var(--text)}
.menu-btn{left:606px;top:22px;width:23px;height:22px;border:1px solid var(--accent);border-radius:2px;padding:6px 5px;display:flex;flex-direction:column;justify-content:space-between}
.menu-btn span{display:block;height:1px;background:var(--accent)}

/* hero */
.hero{left:0;top:66px;width:712px;height:309px;background:linear-gradient(100deg,#b9a48a 0%,#d8c6a8 30%,#c7b9a6 55%,#9aa58a 75%,#5d8a37 100%)}
.hero::after{content:"";position:absolute;inset:0;background:linear-gradient(180deg,rgba(0,0,0,0) 55%,rgba(0,0,0,.45) 100%)}
.hero-arrow{top:140px;z-index:1}
.hero-caption{left:0;top:260px;width:712px;text-align:center;font-family:"Bitter",serif;font-weight:500;font-size:17px;line-height:21px;color:#fff;z-index:1;text-shadow:0 1px 3px rgba(0,0,0,.5)}

/* video */
.video-section{left:0;top:375px;width:712px;height:364px;background:linear-gradient(180deg,#eef0f3 0%,#f3efe9 60%,#f6f3ef 100%)}
.section-title{font-family:"Marcellus",serif;font-size:16px;letter-spacing:.6px;color:var(--ink);text-align:center;width:712px;left:0}
.video-frame{left:161px;top:447px;width:390px;height:216px;background:#fff;padding:4px;box-shadow:0 1px 4px rgba(0,0,0,.2)}
.video-still{width:100%;height:100%;background:linear-gradient(100deg,#8a8e93 0%,#b9b7b2 35%,#45474a 55%,#6d8db3 80%,#c9c7c0 100%);display:flex;align-items:center;justify-content:center}
.search-link{left:0;width:712px;top:684px;text-align:center;font-size:8px;color:var(--accent);text-decoration:underline;letter-spacing:.2px}

/* about */
.about{left:0;top:739px;width:712px;height:253px;background:linear-gradient(180deg,#fff 0%,#f1f1f1 100%)}
.about-title{left:84px;top:778px;font-family:"Marcellus",serif;font-size:15px;color:var(--ink);letter-spacing:.5px}
.about-lead{left:84px;top:812px;width:360px;font-size:7.3px;line-height:12.5px;font-weight:500;color:var(--text)}
.about-body{left:84px;top:843px;width:360px;font-size:7.2px;line-height:12.8px;color:var(--muted)}
.btn{left:84px;top:932px;width:71px;height:18px;background:var(--accent);color:#fff;font-size:7.5px;display:flex;align-items:center;justify-content:center;letter-spacing:.3px}
.about-photo{left:459px;top:782px;width:168px;height:168px;border-radius:50%;background:radial-gradient(circle at 40% 35%,#9fc2e6 0%,#6f9fd0 45%,#c04c4a 80%,#8a6b55 100%)}

/* builders */
.builder-card{top:1063px;width:157px;height:63px;border:1px solid var(--line);background:#fff;display:flex;align-items:center;justify-content:center;font-family:"Jost",sans-serif;font-weight:500;font-size:14px;letter-spacing:1px;color:var(--text)}

/* footer */
.site-footer{left:0;top:1168px;width:712px;height:32px;background:var(--footer);display:flex;align-items:center;justify-content:space-between;padding:0 84px;font-size:7px;color:#eee}
.social{display:flex;gap:7px}
.social span{width:6px;height:6px;border-radius:50%;background:#eee;display:block}
</style>
</head>
<body>

<header class="abs site-header">
  <div class="abs brand">
    <span class="brand-dot"></span>
    <div class="brand-name">Fresh Dwelling<br>Tract Guide</div>
  </div>
  <div class="abs phone">
    <svg width="14" height="14" viewBox="0 0 24 24" fill="none" stroke="#333" stroke-width="1.6"><path d="M5 3h4l2 5-2.5 1.5a11 11 0 0 0 6 6L16 13l5 2v4a2 2 0 0 1-2 2A17 17 0 0 1 3 5a2 2 0 0 1 2-2z"/><path d="M15 3a6 6 0 0 1 6 6M15 7a2 2 0 0 1 2 2"/></svg>
    555-014-2290
  </div>
  <div class="abs menu-btn"><span></span><span></span><span></span></div>
</header>

<section class="abs hero" role="img" aria-label="Smiling couple in front of a new suburban house with a green lawn"></section>
<svg class="abs hero-arrow" style="left:52px" width="12" height="34" viewBox="0 0 12 34"><path d="M11 1 1 17l10 16" fill="none" stroke="#fff" stroke-width="1.2"/></svg>
<svg class="abs hero-arrow" style="left:647px" width="12" height="34" viewBox="0 0 12 34"><path d="M1 1l10 16L1 33" fill="none" stroke="#fff" stroke-width="1.2"/></svg>
<h1 class="abs hero-caption">Looking To Buy Brand New Home From Builders<br>Such As TW Residences, Morvik, P.L. Fennick, Etc.</h1>

<section class="abs video-section" role="img" aria-label="Faded new home exterior in the background"></section>
<h2 class="abs section-title" style="top:413px">WATCH VIDEO</h2>
<div class="abs video-frame">
  <div class="video-still" role="img" aria-label="Agent with a tablet greeting a young couple at a front door">
    <svg width="36" height="36" viewBox="0 0 36 36"><circle cx="18" cy="18" r="16.5" fill="none" stroke="#fff" stroke-width="1.6"/><path d="M14 11v14l11-7z" fill="none" stroke="#fff" stroke-width="1.6" stroke-linejoin="round"/></svg>
  </div>
</div>
<a class="abs search-link">SEARCH FOR NEW HOMES NEAR BY</a>

<section class="abs about"></section>
<h2 class="abs about-title">ABOUT Fresh Dwelling Tract Guide</h2>
<p class="abs about-lead">Lorem ipsum dolor sit amet, consectetuer adipiscing elit, sed diam nonummy nibh euismod tincidunt ut laoreet dolore magna aliquam erat volutpat.</p>
<p class="abs about-body">Lorem ipsum dolor sit amet, consectetuer adipiscing elit, sed diam nonummy nibh euismod tincidunt ut laoreet dolore magna aliquam erat volutpat. Ut wisi enim ad minim veniam, quis nostrud exerci tation ullamcorper suscipit lobortis nisl ut aliquip ex ea commodo consequat. Duis autem vel eum iriure dolor in hendrerit in vulputate velit esse molestie consequat, vel illum dolore eu feugiat nulla facilisis at vero eros et accumsan et iusto odio dignissim qui blandit praesent luptatum zzril delenit augue duis dolore te feugait nulla facilisiUt wisi enim ad minim veniam, quis nostrud .</p>
<a class="abs btn">KNOW MORE</a>
<div class="abs about-photo" role="img" aria-label="Excited couple celebrating outdoors with a signed contract"></div>

<h2 class="abs section-title" style="top:1031px">FEW REPUTED BUILDERS</h2>
<svg class="abs" style="left:54px;top:1084px" width="9" height="22" viewBox="0 0 9 22"><path d="M8 1 1 11l7 10" fill="none" stroke="#aaa" stroke-width="1"/></svg>
<div class="abs builder-card" style="left:105px">TW RESIDENCES</div>
<div class="abs builder-card" style="left:277px">MORVIK</div>
<div class="abs builder-card" style="left:450px">P.L. FENNICK</div>
<svg class="abs" style="left:649px;top:1084px" width="9" height="22" viewBox="0 0 9 22"><path d="M1 1l7 10-7 10" fill="none" stroke="#aaa" stroke-width="1"/></svg>

<footer class="abs site-footer">
  <span>Copyright © 2018 Fresh Dwelling Tract Guide. All Rights Reserved.</span>
  <div class="social"><span></span><span></span><span></span><span></span><span></span></div>
</footer>

</body>
</html>
```